Lanternfield Drinks business cards

We need a business card design for our new logo. The company is modern, progressive, professional, yet approachable. The key products are ready to drink bottles and cans of coffee based beverages.
These cards will be a critical part of the first impression made by our sales organization, business development team, and all external facing personnel.
Card can be a vertical or horizontal orientation.

Target Market(s)

Customers, suppliers, business partners

Industry/Entity Type

Business

Contact Information for Business Card

Business cards should feature Company Name and Logo.

Font styles to use
Serif

Colors

Designer to choose colors to be used in the design.

Requirements
Must have
• Strong readability of Name, phone #, mobile number and email address.
• Job title, website url, Street Address, and other details can be secondary level readability.
Nice to have
• High impact, simplistic quality design.
• Ok to utilize the 'H in the box' separate from the company name

```html
<!DOCTYPE html>
<html lang="en">
<head>
<meta charset="utf-8">
<title>Lanternfield Drinks – Business Cards</title>
<link rel="stylesheet" href="https://fonts.googleapis.com/css2?family=Cinzel:wght@700&family=Raleway:wght@400;500&display=swap">
<style>
  :root {
    --page-bg: #1c1c1d;
    --card-dark: #2a2829;
    --card-dark-deep: #1f1d1e;
    --orange-light: #f2894a;
    --orange: #e96a30;
    --gold: #d9ad45;
    --gold-box: #c9a441;
    --white: #ffffff;
    --text-soft: #e9e4e0;
  }
  * { box-sizing: border-box; margin: 0; padding: 0; }
  html, body {
    width: 1200px; height: 864px; overflow: hidden;
    background: var(--page-bg);
  }
  .sheet {
    position: relative; width: 1200px; height: 864px;
    display: flex; align-items: center; justify-content: center; gap: 50px;
  }
  .card {
    position: relative; width: 525px; height: 300px; overflow: hidden;
    background: linear-gradient(160deg, var(--card-dark), var(--card-dark-deep));
    box-shadow: 0 18px 40px rgba(0,0,0,.55);
  }

  /* Brand lockup */
  .brand { display: flex; align-items: center; gap: 16px; }
  .brand-mark { width: 58px; height: 58px; border: 4px solid currentColor; flex: none; }
  .brand-name {
    font-family: "Cinzel", Georgia, serif; font-weight: 700;
    font-size: 30px; letter-spacing: .5px; line-height: 1;
  }

  /* Front */
  .card-front .band {
    height: 140px; padding: 0 34px;
    display: flex; align-items: center;
    background: linear-gradient(120deg, var(--orange), var(--orange-light) 70%, var(--orange));
    color: var(--white);
  }
  .contact {
    position: absolute; left: 34px; top: 160px;
    font-family: "Raleway", Arial, sans-serif; font-size: 12px;
    color: var(--text-soft); line-height: 1.35;
  }
  .contact address { font-style: normal; margin-bottom: 8px; }
  .contact ul { list-style: none; }
  .contact li { display: flex; align-items: center; gap: 9px; margin-bottom: 4px; font-weight: 500; }
  .contact svg { width: 12px; height: 12px; flex: none; }
  .person {
    position: absolute; right: 34px; bottom: 26px; width: 150px; text-align: center;
  }
  .person-name {
    font-family: "Cinzel", Georgia, serif; font-weight: 700;
    font-size: 13px; color: var(--white); margin-bottom: 6px; letter-spacing: .3px;
  }
  .person-title {
    background: var(--gold-box); color: var(--white);
    font-family: "Raleway", Arial, sans-serif; font-size: 11px;
    padding: 10px 0;
  }

  /* Back */
  .card-back { display: flex; align-items: center; justify-content: center; color: var(--orange); }
  .card-back .brand-name { font-size: 34px; }
  .card-back .rule {
    position: absolute; left: 50%; top: 186px; width: 300px; height: 2px;
    transform: translateX(-30%); background: var(--gold);
  }
</style>
</head>
<body>
<main class="sheet">

  <section class="card card-front" aria-label="Business card front">
    <div class="band">
      <div class="brand">
        <span class="brand-mark" aria-hidden="true"></span>
        <span class="brand-name">Lanternfield Drinks</span>
      </div>
    </div>

    <div class="contact">
      <address>418 Harbor Lane<br>Millbrook, NY 12545</address>
      <ul>
        <li>
          <svg viewBox="0 0 12 12" aria-hidden="true"><rect x=".5" y=".5" width="11" height="11" fill="none" stroke="#e96a30"/><path d="M3.5 3h2l.6 1.6-1 .7a5 5 0 0 0 1.7 1.7l.7-1 1.5.6v2c-3.2 0-5.5-2.4-5.5-5.6z" fill="#e96a30"/></svg>
          555.210.4830
        </li>
        <li>
          <svg viewBox="0 0 12 12" aria-hidden="true"><rect x=".5" y=".5" width="11" height="11" fill="none" stroke="#e96a30"/><rect x="4" y="2.5" width="4" height="7" rx=".6" fill="none" stroke="#e96a30"/></svg>
          555.318.7762
        </li>
        <li>
          <svg viewBox="0 0 12 12" aria-hidden="true"><rect x=".5" y=".5" width="11" height="11" fill="none" stroke="#e96a30"/><path d="M2.5 3.5h7v5h-7zM2.5 3.5 6 6.5l3.5-3" fill="none" stroke="#e96a30"/></svg>
          dan@lanternfielddrinks.com
        </li>
        <li>
          <svg viewBox="0 0 12 12" aria-hidden="true"><rect x=".5" y=".5" width="11" height="11" fill="none" stroke="#e96a30"/><circle cx="6" cy="6" r="3.2" fill="none" stroke="#e96a30"/><path d="M2.8 6h6.4M6 2.8c-1.6 2-1.6 4.4 0 6.4M6 2.8c1.6 2 1.6 4.4 0 6.4" fill="none" stroke="#e96a30" stroke-width=".7"/></svg>
          www.lanternfielddrinks.com
        </li>
      </ul>
    </div>

    <div class="person">
      <p class="person-name">DANIEL WHITCOMBE</p>
      <p class="person-title">Managing Director</p>
    </div>
  </section>

  <section class="card card-back" aria-label="Business card back">
    <div class="brand">
      <span class="brand-mark" aria-hidden="true"></span>
      <span class="brand-name">Lanternfield Drinks</span>
    </div>
    <span class="rule" aria-hidden="true"></span>
  </section>

</main>
</body>
</html>
```